RWT Fittings Ltd Business Cards

We need a business card with our business logo. We provide window and door installations on high-rises in west coast British Colombia, Canada.

I would like my business information and details on one side of the card, and the other side the company name with logo

Target Market(s)

General Contractors

Industry/Entity Type

Construction

Contact Information for Business Card

one side i want my company name and logo in the dark theme logo that i provided

Requirements
Must have
• Marco Peltieri, 16045518293, RWTFittings@mailbox-demo.com, 1407-5194 Linden Row Burnaby BC, V5H 2K9, Owner & Manager

```html
<!DOCTYPE html>
<html lang="en">
<head>
<meta charset="utf-8">
<title>RWT Fittings Ltd – Business Cards</title>
<link rel="stylesheet" href="https://fonts.googleapis.com/css2?family=Roboto:wght@400;500;700&display=swap">
<style>
  :root {
    --stage: #232323;
    --card-dark: #202125;
    --brand-blue: #29aae2;
    --ink-white: #ffffff;
    --ink-grey: #8e8f93;
    --swoosh-grey: #9a9a9a;
  }
  * { box-sizing: border-box; margin: 0; padding: 0; }
  html, body { width: 1200px; height: 780px; overflow: hidden; }
  body {
    background: var(--stage);
    font-family: "Roboto", Arial, sans-serif;
    position: relative;
  }
  .card {
    position: absolute;
    top: 240px;
    width: 500px;
    height: 300px;
    overflow: hidden;
  }
  .card--info { left: 60px; background: var(--card-dark); }
  .card--brand { left: 640px; background: var(--brand-blue); }

  .card__swoosh { position: absolute; inset: 0; }

  .wordmark {
    display: flex;
    align-items: center;
    gap: 10px;
    font-weight: 700;
    white-space: nowrap;
  }
  .wordmark__square { display: block; flex: none; }

  .card--info .wordmark {
    position: absolute;
    left: 30px;
    top: 70px;
    font-size: 20px;
    color: var(--brand-blue);
  }
  .card--info .wordmark__square { width: 16px; height: 16px; background: var(--brand-blue); }

  .card__divider {
    position: absolute;
    left: 250px;
    top: 45px;
    width: 2px;
    height: 170px;
    background: var(--ink-white);
  }

  .contact {
    position: absolute;
    left: 272px;
    top: 82px;
    color: var(--ink-white);
  }
  .contact__name { font-size: 24px; font-weight: 700; line-height: 1.1; white-space: nowrap; }
  .contact__name .first { color: var(--brand-blue); }
  .contact__name .last { color: var(--ink-grey); }
  .contact__role { font-size: 12px; font-weight: 500; margin-top: 3px; }
  .contact__address { font-size: 12px; line-height: 1.4; margin-top: 10px; font-style: normal; }
  .contact__line {
    display: flex; align-items: center; gap: 6px;
    font-size: 12px; line-height: 1.5; white-space: nowrap;
  }
  .contact__line:first-of-type { margin-top: 6px; }
  .contact__icon { width: 12px; height: 12px; flex: none; }

  .card--brand .wordmark {
    position: absolute;
    left: 50%; top: 50%;
    transform: translate(-50%, -50%);
    font-size: 34px;
    color: var(--card-dark);
  }
  .card--brand .wordmark__square { width: 26px; height: 26px; background: var(--card-dark); }
</style>
</head>
<body>

  <section class="card card--info" aria-label="Business card, contact side">
    <svg class="card__swoosh" viewBox="0 0 500 300" aria-hidden="true">
      <path d="M0 190 C70 250 200 292 420 300 L0 300 Z" fill="var(--brand-blue)"/>
      <path d="M120 252 C210 285 300 296 420 300" fill="none" stroke="var(--swoosh-grey)" stroke-width="5"/>
    </svg>

    <div class="wordmark">
      <span class="wordmark__square"></span>
      <span class="wordmark__name">RWT Fittings Ltd</span>
    </div>

    <div class="card__divider"></div>

    <div class="contact">
      <p class="contact__name"><span class="first">Marco</span> <span class="last">Peltieri</span></p>
      <p class="contact__role">Owner &amp; Manager</p>
      <address class="contact__address">1407-5194 Linden Row<br>Burnaby BC, V5H 2K9</address>
      <p class="contact__line">
        <svg class="contact__icon" viewBox="0 0 24 24" aria-hidden="true"><path fill="var(--brand-blue)" d="M6.6 10.8a15.1 15.1 0 0 0 6.6 6.6l2.2-2.2a1 1 0 0 1 1-.25 11.4 11.4 0 0 0 3.6.57 1 1 0 0 1 1 1V20a1 1 0 0 1-1 1A17 17 0 0 1 3 4a1 1 0 0 1 1-1h3.5a1 1 0 0 1 1 1c0 1.25.2 2.45.57 3.57a1 1 0 0 1-.25 1z"/></svg>
        <span>1604 551 8293</span>
      </p>
      <p class="contact__line">
        <svg class="contact__icon" viewBox="0 0 24 24" aria-hidden="true"><rect x="2" y="5" width="20" height="14" rx="2" fill="var(--brand-blue)"/><path d="M3 6l9 7 9-7" fill="none" stroke="var(--card-dark)" stroke-width="2"/></svg>
        <span>RWTFittings@mailbox-demo.com</span>
      </p>
    </div>
  </section>

  <section class="card card--brand" aria-label="Business card, brand side">
    <div class="wordmark">
      <span class="wordmark__square"></span>
      <span class="wordmark__name">RWT Fittings Ltd</span>
    </div>
  </section>

</body>
</html>
```